Lumavento business card

We need a modern business card - With our 4 colors - See web: www.lumavento.dk

I have attached logo and som old business Cards we have - Lets Make the new ones shine...:-) -

Industry/Entity Type

Business

Requirements
Must have
• the logo with lumavento only,

```html
<!DOCTYPE html>
<html lang="da">
<head>
<meta charset="utf-8">
<title>Lumavento – visitkort</title>
<link rel="stylesheet" href="https://fonts.googleapis.com/css2?family=Source+Sans+3:wght@300;400;600&display=swap">
<style>
  :root {
    --stage: #161616;
    --card-light: #f3f3f3;
    --magenta: #e8008a;
    --lime: #9cc43a;
    --ink: #1d1d1d;
    --ink-soft: #3a3a3a;
    --white: #ffffff;
    --hairline: #e4e4e4;
  }
  * { margin: 0; padding: 0; box-sizing: border-box; }
  html, body {
    width: 1200px; height: 900px; overflow: hidden;
    background: var(--stage);
    font-family: "Source Sans 3", "Myriad Pro", sans-serif;
  }
  .canvas { position: relative; width: 1200px; height: 900px; }

  .card {
    position: absolute; top: 184px;
    width: 302px; height: 491px;
    border-radius: 14px;
    text-align: center;
  }
  .card--front { left: 299px; background: var(--card-light); color: var(--ink); }
  .card--back { left: 645px; width: 305px; background: var(--magenta); color: var(--white); }

  .brand {
    position: absolute; top: 138px; left: 0; right: 0;
    display: flex; justify-content: center; align-items: center; gap: 8px;
  }
  .brand__dot { width: 12px; height: 12px; border-radius: 50%; background: var(--lime); }
  .brand__name {
    font-weight: 300; font-size: 21px; letter-spacing: 2.5px; color: var(--ink-soft);
  }
  .brand__rule {
    position: absolute; top: 180px; left: 34px; width: 235px; height: 3px; background: var(--lime);
  }
  .tagline {
    position: absolute; top: 193px; left: 0; right: 0;
    font-size: 15px; font-weight: 400; color: var(--ink-soft);
  }
  .tagline-rule {
    position: absolute; top: 216px; left: 16px; right: 16px; height: 1px; background: var(--hairline);
  }

  .person { position: absolute; top: 259px; left: 0; right: 0; }
  .person__name {
    font-size: 19px; font-weight: 600; color: var(--magenta); letter-spacing: 0.2px; line-height: 1.2;
  }
  .person__role { font-size: 13.5px; margin-top: 3px; }

  .contact { position: absolute; top: 335px; left: 0; right: 0; list-style: none; }
  .contact li {
    display: flex; justify-content: center; align-items: center; gap: 3px;
    font-size: 14px; line-height: 21px;
  }
  .contact svg { width: 11px; height: 11px; fill: var(--magenta); }

  .address { position: absolute; top: 427px; left: 0; right: 0; font-size: 14px; line-height: 17px; font-style: normal; }

  .back__name {
    position: absolute; top: 412px; left: 0; right: 0;
    font-size: 15px; letter-spacing: 1.6px;
  }
  .back__rule {
    position: absolute; top: 435px; left: 27px; width: 251px; height: 3px; background: var(--white); border-radius: 2px;
  }
  .back__role {
    position: absolute; top: 440px; left: 0; right: 0;
    font-size: 14px; letter-spacing: 1.6px;
  }
</style>
</head>
<body>
<main class="canvas">
  <section class="card card--front">
    <div class="brand">
      <span class="brand__dot"></span>
      <span class="brand__name">lumavento</span>
    </div>
    <div class="brand__rule"></div>
    <p class="tagline">Medier til unge</p>
    <div class="tagline-rule"></div>

    <div class="person">
      <h1 class="person__name">JONAS HAVEMARK</h1>
      <p class="person__role">Salgsdirektor</p>
    </div>

    <ul class="contact">
      <li>
        <svg viewBox="0 0 24 24" aria-hidden="true"><path d="M6.6 10.8a15.1 15.1 0 0 0 6.6 6.6l2.2-2.2a1 1 0 0 1 1-.25 11.4 11.4 0 0 0 3.6.57 1 1 0 0 1 1 1V20a1 1 0 0 1-1 1A17 17 0 0 1 3 4a1 1 0 0 1 1-1h3.5a1 1 0 0 1 1 1c0 1.25.2 2.46.57 3.6a1 1 0 0 1-.25 1z"/></svg>
        +45 20 31 47 62
      </li>
      <li>
        <svg viewBox="0 0 24 24" aria-hidden="true"><path d="M2 5h20v14H2z M2 5l10 8 10-8" /><path d="M3 6l9 7 9-7" fill="#fff" opacity=".6"/></svg>
        jh@lumavento.dk
      </li>
      <li>
        <svg viewBox="0 0 24 24" aria-hidden="true"><circle cx="12" cy="12" r="11"/><path d="M7 7c2 1 3 3 2 5s1 3 2 5M15 4c-1 2 0 3 2 4s3 3 2 6" stroke="#fff" stroke-width="1.6" fill="none"/></svg>
        www.lumavento.dk
      </li>
    </ul>

    <address class="address">Lindholms Allé 18 - 2000<br>Frederiksberg -Tlf. 38 14 60 92</address>
  </section>

  <section class="card card--back">
    <p class="back__name">Jonas Havemark</p>
    <div class="back__rule"></div>
    <p class="back__role">Salgsdirektør</p>
  </section>
</main>
</body>
</html>
```